Flat bootstrap design for existing site

I'm looking for a modern flat design based around an existing logo. This has to be a custom design (no external templates), and implemented into a bootstrap framework.

The logo is attached as 2 versions - choose whichever you want, that flows better with whatever design you choose.

Added screenshots of the existing site (currently using the default bootstrap layouts). Please make your designs around those pages in the screenshots (i.e. the homepage only has the postal code input and the header). The active page has 3 screenshots, because I wanted to illustrate the other states that would be visible (in the table rows).

This is a moving/junk removal website, just for some context.

Here's some example websites (flat designs) that I like, just to give you an idea of what I'm after.

https://www.plimvora.com/
https://dacklow.com/
https://trevanu.com/
https://quobrintal.com/en/

Coding

Coded - Design and coding required

Number of Pages Required

5+ page

Colors

Designer to choose colors to be used in the design.

Requirements
Must have
• It must be a modern/simple flat design, that is built around the existing logo (attached).
• It has to be implemented using bootstrap.

```html
<!DOCTYPE html>
<html lang="en">
<head>
<meta charset="utf-8">
<title>Haulvo – Booking Details</title>
<link href="https://fonts.googleapis.com/css2?family=Nunito+Sans:wght@400;600;700;800&display=swap" rel="stylesheet">
<style>
  :root {
    --brand: #3ec4f0;
    --accent: #f15a24;
    --page-bg: #e9e9eb;
    --card-bg: #ffffff;
    --ink: #1b1b1b;
    --muted: #6f6f6f;
    --line: #c9c9c9;
    --table-head: #f2f2f2;
  }
  * { box-sizing: border-box; margin: 0; padding: 0; }
  html, body { width: 1200px; height: 1022px; overflow: hidden; }
  body {
    background: var(--page-bg);
    font-family: "Nunito Sans", sans-serif;
    color: var(--ink);
    position: relative;
  }
  .site-header {
    position: absolute; left: 0; top: 0; width: 1200px; height: 85px;
    background: var(--card-bg);
  }
  .brand {
    position: absolute; left: 131px; top: 24px;
    display: flex; align-items: center; gap: 8px;
    font-size: 30px; font-weight: 800; color: var(--brand); letter-spacing: 1px;
  }
  .brand-dot { width: 14px; height: 14px; border-radius: 50%; background: var(--brand); }
  .main-nav a {
    position: absolute; top: 33px; font-size: 11px; color: var(--ink);
    text-decoration: none; letter-spacing: .2px;
  }
  .nav-book { left: 635px; }
  .nav-how { left: 696px; }
  .nav-driver {
    left: 804px; top: 26px !important; width: 126px; height: 29px;
    border: 1px solid var(--brand); color: var(--brand) !important;
    display: flex; align-items: center; justify-content: center;
  }
  .account {
    position: absolute; left: 947px; top: 32px; font-size: 11px;
    display: flex; align-items: center; gap: 10px;
  }
  .card { position: absolute; left: 132px; width: 937px; background: var(--card-bg); }
  .booking-card { top: 118px; height: 430px; }
  .drivers-card { top: 586px; height: 391px; }
  .card-title {
    position: absolute; left: 30px; font-size: 21px; font-weight: 700;
    color: var(--brand); letter-spacing: .3px;
  }
  .booking-card .card-title { top: 21px; }
  .drivers-card .card-title { top: 22px; }
  .field-label { position: absolute; font-size: 11.5px; }
  .field {
    position: absolute; border: 1px solid var(--line); height: 46px;
    font-size: 11px; color: var(--muted); padding: 0 16px;
    display: flex; align-items: center; justify-content: space-between;
  }
  .field-area { align-items: flex-start; padding-top: 13px; height: 119px; }
  .btn-update {
    position: absolute; left: 386px; top: 352px; width: 164px; height: 45px;
    background: var(--brand); color: #fff; font-size: 19px; font-weight: 700;
    display: flex; align-items: center; justify-content: center; letter-spacing: .5px;
  }
  .intro { position: absolute; left: 30px; top: 55px; font-size: 14px; }
  .drivers-table {
    position: absolute; left: 31px; top: 102px; width: 877px; height: 254px;
    border: 1px solid var(--line);
  }
  .table-head {
    height: 45px; background: var(--table-head); border-bottom: 1px solid var(--line);
    position: relative; font-size: 11.5px; font-weight: 700;
  }
  .table-head span { position: absolute; top: 15px; }
  .row { position: absolute; left: 18px; width: 830px; font-size: 12.5px; }
  .row + .row { border-top: 1px solid #dcdcdc; }
  .row span { position: absolute; }
  .col-name { left: 15px; }
  .col-dist { left: 219px; }
  .dash { left: 404px; width: 15px; height: 1px; background: var(--ink); }
  .status {
    left: 673px; width: 122px; height: 26px; background: var(--accent);
    color: #fff; font-size: 11.5px; font-weight: 600;
    display: flex; align-items: center; justify-content: center;
  }
</style>
</head>
<body>
  <header class="site-header">
    <div class="brand"><span class="brand-dot"></span>HAULVO</div>
    <nav class="main-nav">
      <a class="nav-book" href="#">BOOK</a>
      <a class="nav-how" href="#">HOW IT WORKS</a>
      <a class="nav-driver" href="#">BECOME A DRIVER</a>
    </nav>
    <div class="account">dana@mailquarry.com
      <svg width="10" height="6" viewBox="0 0 10 6"><path d="M1 1l4 4 4-4" fill="none" stroke="#555" stroke-width="1.2"/></svg>
    </div>
  </header>

  <section class="card booking-card">
    <h2 class="card-title">BOOKING DETAILS</h2>
    <label class="field-label" style="left:43px;top:86px">PACKAGE SELECTED</label>
    <div class="field" style="left:43px;top:112px;width:389px">PACKAGE 1
      <svg width="11" height="7" viewBox="0 0 11 7"><path d="M1 1l4.5 4.5L10 1" fill="none" stroke="#555" stroke-width="1.3"/></svg>
    </div>
    <label class="field-label" style="left:476px;top:86px">PICK UP TIME SELECTED</label>
    <div class="field" style="left:476px;top:112px;width:389px">JULY 17 AT 8.30 PM
      <svg width="16" height="16" viewBox="0 0 16 16" fill="none" stroke="#777" stroke-width="1"><rect x="1" y="2.5" width="14" height="12.5"/><path d="M1 6h14M4.5 1v3M11.5 1v3M4.7 6v9M8 6v9M11.3 6v9M1 9h14M1 12h14"/></svg>
    </div>
    <label class="field-label" style="left:43px;top:179px">DESCRIPTION</label>
    <div class="field field-area" style="left:43px;top:205px;width:822px">1 LARGE STOVE</div>
    <div class="btn-update">UPDATE</div>
  </section>

  <section class="card drivers-card">
    <h2 class="card-title">DRIVERS IN YOUR AREA</h2>
    <p class="intro">Please stay on this page and be patient, while we contact the drivers and find you one ASAP</p>
    <div class="drivers-table">
      <div class="table-head">
        <span style="left:31px">NAME</span>
        <span style="left:236px">DISTANCE (KM)</span>
        <span style="left:416px">AGREED PICKUP TIME</span>
      </div>
      <div class="row" style="top:46px;height:58px">
        <span class="col-name" style="top:29px">Perry Holt</span>
        <span class="col-dist" style="top:29px">4.04km Away</span>
        <span class="dash" style="top:42px"></span>
        <span class="status" style="top:18px">PENDING</span>
      </div>
      <div class="row" style="top:104px;height:46px">
        <span class="col-name" style="top:17px">Simon Darrow</span>
        <span class="col-dist" style="top:17px">5.7km Away</span>
        <span class="dash" style="top:30px"></span>
        <span class="status" style="top:10px">PENDING</span>
      </div>
      <div class="row" style="top:150px;height:51px">
        <span class="col-name" style="top:17px">Alden Price</span>
        <span class="col-dist" style="top:17px">11.13km Away</span>
        <span class="dash" style="top:30px"></span>
        <span class="status" style="top:11px">PENDING</span>
      </div>
      <div class="row" style="top:201px;height:52px">
        <span class="col-name" style="top:13px">Wes Marlowe</span>
        <span class="col-dist" style="top:13px">11.91km Away</span>
        <span class="dash" style="top:26px"></span>
        <span class="status" style="top:14px">PENDING</span>
      </div>
    </div>
  </section>
</body>
</html>
```